Social responsible Renewable Energy company

We at brivoX are an independent power producer company founded in 2021 that handles large scale deployment of Renewable Energy and carbon neutral Energy as a service model. We offer turnkey solutions using solar panel systems and this could be incorporated in our business cards. You can also find our logo in the documents provided. Another key issue is that the business cards will be printed on recicled paper, not sure if this is a limitation in deciding the design. The recycled sign should also be added on the business card and stating that the paper used was recycled. Our website is www.mybrivox-example.com. It should also be very professional, not too dreamy but still needs to capture your imagination. We are really excited to get your ideas !

Target Market(s)

Renewable Energy market

Contact Information for Business Card

The business card will be printed on recycled paper. Name of the company is brivoX. Website is www.mybrivox-example.com

Requirements
Nice to have
• Our motto: Powered by renewable, driven by people.

```html
<!DOCTYPE html>
<html lang="en">
<head>
<meta charset="utf-8">
<title>brivoX business card</title>
<link rel="stylesheet" href="https://fonts.googleapis.com/css2?family=Montserrat:wght@400;500;700&display=swap">
<style>
  :root{
    --bg:#e9e9e7;
    --card:#ffffff;
    --navy:#0b3f7f;
    --blue:#1d63b0;
    --green:#7cc242;
    --badge:#1f5a2a;
    --panel:#bfe0f2;
    --panel-edge:#9ccbe6;
    --shadow:rgba(0,0,0,.18);
  }
  *{box-sizing:border-box;margin:0;padding:0}
  html,body{width:1200px;height:1200px;overflow:hidden}
  body{background:var(--bg);font-family:"Montserrat",sans-serif;position:relative}
  .card{
    position:absolute;left:220px;width:760px;height:434px;
    background:var(--card);box-shadow:0 14px 34px var(--shadow);overflow:hidden;
  }
  .card--front{top:120px}
  .card--back{top:640px}

  .wordmark{color:var(--navy);font-weight:700;letter-spacing:1px;line-height:1}
  .card--front .wordmark{position:absolute;left:310px;top:110px;font-size:78px}
  .recycled-badge{position:absolute;left:370px;top:222px;width:86px;height:50px;background:var(--badge);border-radius:3px}
  .front-web{position:absolute;left:120px;top:300px;font-size:24px;font-weight:500;color:var(--green)}
  .solar-panel{position:absolute;right:0;bottom:0;width:190px;height:150px;
    background:linear-gradient(135deg,var(--panel),var(--panel-edge));}

  .person{position:absolute;left:48px;top:44px}
  .person__name{font-size:28px;font-weight:700;color:var(--navy)}
  .person__role{font-size:17px;font-weight:500;color:var(--navy);margin-top:4px}
  .divider{position:absolute;left:150px;top:128px;width:560px;height:1.5px;background:var(--blue)}
  .contact{position:absolute;font-size:17px;color:var(--navy);list-style:none}
  .contact li{display:flex;align-items:center;gap:10px;margin-bottom:10px}
  .contact svg{width:18px;height:18px;flex:none}
  .contact--left{left:48px;top:150px}
  .contact--right{left:330px;top:300px}
  .card--back .wordmark{position:absolute;right:60px;top:180px;font-size:52px}
  .corner-stripes{position:absolute;left:0;bottom:0}
</style>
</head>
<body>
  <section class="card card--front" aria-label="Card front">
    <div class="wordmark">brivoX</div>
    <div class="recycled-badge" role="img" aria-label="Recycled paper certification badge"></div>
    <div class="front-web">www.mybrivox-example.com</div>
    <div class="solar-panel" role="img" aria-label="Solar panel illustration"></div>
  </section>

  <section class="card card--back" aria-label="Card back">
    <div class="person">
      <div class="person__name">Dana Reyes</div>
      <div class="person__role">CEO</div>
    </div>
    <div class="divider"></div>
    <ul class="contact contact--left">
      <li><svg viewBox="0 0 24 24" fill="none" stroke="currentColor" stroke-width="1.6"><path d="M5 3h4l2 5-2.5 1.5a11 11 0 0 0 6 6L16 13l5 2v4a2 2 0 0 1-2 2A16 16 0 0 1 3 5a2 2 0 0 1 2-2z"/></svg>555 010-4821</li>
      <li><svg viewBox="0 0 24 24" fill="none" stroke="currentColor" stroke-width="1.6"><rect x="3" y="5" width="18" height="14" rx="1"/><path d="M3 6l9 7 9-7"/></svg>info@mybrivox-example.com</li>
    </ul>
    <div class="wordmark">brivoX</div>
    <ul class="contact contact--right">
      <li><svg viewBox="0 0 24 24" fill="none" stroke="currentColor" stroke-width="1.6"><circle cx="12" cy="12" r="9"/><path d="M3 12h18M12 3c3 3 3 15 0 18M12 3c-3 3-3 15 0 18"/></svg>www.mybrivox-example.com</li>
      <li><svg viewBox="0 0 24 24" fill="none" stroke="currentColor" stroke-width="1.6"><path d="M4 11l8-7 8 7v9h-5v-6H9v6H4z"/></svg>48 Harbor Lane, Suite 200, GA 30000</li>
    </ul>
    <svg class="corner-stripes" width="300" height="60" viewBox="0 0 300 60" aria-hidden="true">
      <polygon points="0,18 24,18 16,30 0,30" fill="var(--green)"/>
      <polygon points="30,18 50,18 42,30 22,30" fill="var(--green)"/>
      <polygon points="0,40 300,40 300,60 0,60" fill="var(--blue)"/>
    </svg>
  </section>
</body>
</html>
```